Marwick Family Chiropractic Stationary

The letterhead and business card must have our logo.
We would like to see the logo used in different ways ( It can be expanded upon in the stationary.)
Please use the the same or similar colors.
Must be eye catching and memorable.
Must be easy to read

Reason: The doctor has been too busy to make any final decisions. He would like to give himself a little more time.

Target Market(s)

Chiropractic Healthcare

Industry/Entity Type

Business

Requirements
Must have
• Dr. Leonard Marwick D.C.
Chiropractor

555-555-0183

417 Birchfield Road, 2nd Floor
Ashmere, NW 40591

drmarwick@marwickspine.example
www.marwickspine.example
www.facebook.com/MarwickFamilySpine
Should not have
• should not be difficult to read

```html
<!DOCTYPE html>
<html lang="en">
<head>
<meta charset="utf-8">
<title>Marwick Family Chiropractic – Business Cards</title>
<link rel="stylesheet" href="https://fonts.googleapis.com/css2?family=Montserrat:wght@500;700&family=Open+Sans:wght@400;600;700&display=swap">
<style>
  :root {
    --backdrop: #d6d6d4;
    --card-black: #070707;
    --leaf-green: #a8cf5e;
    --band-green: #9ccc4f;
    --line-green: #3f9a3c;
    --taupe: #857362;
    --taupe-light: #a39585;
    --ink-dark: #1b1b1b;
    --white: #ffffff;
  }
  * { box-sizing: border-box; margin: 0; padding: 0; }
  html, body { width: 1200px; height: 720px; overflow: hidden; }
  body {
    background: var(--backdrop);
    font-family: "Open Sans", Arial, sans-serif;
    position: relative;
  }
  .card {
    position: absolute;
    width: 550px;
    height: 315px;
    border-radius: 26px 0 26px 0;
    overflow: hidden;
    text-align: center;
  }
  .card--contact { left: 40px; top: 28px; background: var(--card-black); }
  .card--brand { left: 613px; top: 28px; background: var(--card-black); }
  .card--taupe { left: 40px; top: 369px; background: var(--taupe); }
  .card--green { left: 613px; top: 369px; background: var(--leaf-green); }

  .logo-mark {
    position: absolute;
    left: 50%;
    transform: translateX(-50%);
    border-radius: 50% 50% 12px 12px;
  }
  .card--contact .logo-mark {
    top: 16px; width: 92px; height: 96px;
    background: radial-gradient(circle at 50% 40%, #c9d94a, #5e9b3a 70%, #6d5f52);
  }
  .logo-name {
    font-family: "Montserrat", Arial, sans-serif;
    font-weight: 700;
    color: var(--leaf-green);
  }
  .logo-name .second { color: var(--taupe-light); }
  .card--contact .logo-name { position: absolute; top: 124px; left: 0; right: 0; }
  .card--contact .logo-name .first { display: block; font-size: 25px; letter-spacing: 1px; line-height: 1; }
  .card--contact .logo-name .second { display: block; font-size: 11px; letter-spacing: 1px; margin-top: 3px; }

  .name-band {
    position: absolute;
    top: 188px; left: 0; right: 0;
    height: 32px;
    background: var(--band-green);
    box-shadow: 0 -6px 0 -3px var(--line-green), 0 6px 0 -3px var(--line-green);
    display: flex; align-items: center; justify-content: center;
    font-size: 15px; color: var(--ink-dark);
  }
  .name-band .doctor { font-weight: 700; padding-right: 7px; border-right: 1px solid var(--ink-dark); }
  .name-band .role { padding-left: 7px; }

  .contact-list {
    position: absolute;
    top: 236px; left: 0; right: 0;
    color: var(--white); font-size: 12.5px; line-height: 21px;
  }
  .contact-row { display: flex; justify-content: center; gap: 14px; }
  .contact-item { display: inline-flex; align-items: center; gap: 5px; }
  .dot { width: 7px; height: 7px; border-radius: 50%; background: var(--leaf-green); display: inline-block; }
  .address { margin-top: 3px; font-size: 13px; }

  .card--brand .logo-mark {
    top: 10px; width: 260px; height: 265px;
    background: radial-gradient(circle, #26301f, #121610 70%);
    opacity: 0.9;
  }
  .card--brand .logo-name { position: absolute; top: 94px; left: 0; right: 0; }
  .card--brand .logo-name .first { display: block; font-size: 58px; line-height: 1; letter-spacing: 2px; }
  .card--brand .logo-name .second { display: block; font-size: 24px; letter-spacing: 2px; margin-top: 8px; }

  .web {
    position: absolute; left: 0; right: 0; bottom: 24px;
    color: var(--white); font-size: 14px; letter-spacing: 2px;
  }
  .card--taupe .logo-mark, .card--green .logo-mark {
    top: 26px; width: 200px; height: 210px;
    background: radial-gradient(circle at 50% 40%, rgba(255,255,255,0.85), rgba(255,255,255,0.35) 72%);
  }
</style>
</head>
<body>
  <section class="card card--contact">
    <div class="logo-mark" role="img" aria-label="Marwick Family Chiropractic tree logo with colourful leaves"></div>
    <div class="logo-name"><span class="first">MARWICK</span><span class="second">FAMILY CHIROPRACTIC</span></div>
    <div class="name-band"><span class="doctor">Dr. Leonard Marwick D.C.</span><span class="role">Chiropractor</span></div>
    <div class="contact-list">
      <div class="contact-row">
        <span class="contact-item">
          <svg width="10" height="10" viewBox="0 0 10 10" aria-hidden="true"><path d="M2 1 L4 1 L4.6 3 L3.4 4 Q4.5 6 6 6.6 L7 5.4 L9 6 L9 8 Q8.5 9 7 9 Q1 8 1 2 Q1 1 2 1Z" fill="#e9d44a"/></svg>
          555-555-0183</span>
        <span class="contact-item"><span class="dot"></span>mymarwick@marwickspine.example</span>
      </div>
      <div class="contact-row">
        <span class="contact-item"><span class="dot"></span>www.marwickspine.example</span>
        <span class="contact-item"><span class="dot"></span>MarwickFamilySpine</span>
      </div>
      <div class="address">417 Birchfield Road, 2nd Floor, Ashmere, NW 40591</div>
    </div>
  </section>

  <section class="card card--brand">
    <div class="logo-mark" role="img" aria-label="Faint large tree logo in the background"></div>
    <div class="logo-name"><span class="first">MARWICK</span><span class="second">FAMILY CHIROPRACTIC</span></div>
    <div class="web">www.marwickspine.example</div>
  </section>

  <section class="card card--taupe">
    <div class="logo-mark" role="img" aria-label="White tree logo mark"></div>
    <div class="web">www.marwickspine.example</div>
  </section>

  <section class="card card--green">
    <div class="logo-mark" role="img" aria-label="White tree logo mark"></div>
    <div class="web">www.marwickspine.example</div>
  </section>
</body>
</html>
```